Inspirational Quotes Poster Set

Brookloft is a stylish coworking space, which has a design-oriented vintage look from the 60's with an industrial touch (www.brookloft-example.com) Brookloft Quote Poster Set of 16 posters. The poster should be typo oriented and rather simple. Reflecting a bit the clean billboard design from the sixties. Minimal / simple graphical elements

Target Market(s)

Startups and Entrepreneurs

Industry/Entity Type

Startup

Font styles to use
Sans Serif

Colors

Designer to choose colors to be used in the design.

Requirements
Must have
• Posters need to be on and very stylish

```html
<!DOCTYPE html>
<html lang="en">
<head>
<meta charset="utf-8">
<title>Brookloft Quote Poster Set</title>
<link rel="stylesheet" href="https://fonts.googleapis.com/css2?family=Josefin+Sans:wght@600&family=Carlito&display=swap">
<style>
  :root {
    --poster-red: #b34a53;
    --frame-grey: #d3d3d3;
    --ink-white: #ffffff;
  }
  html, body {
    margin: 0;
    padding: 0;
    width: 1200px;
    height: 675px;
    overflow: hidden;
    background: var(--poster-red);
  }
  .poster {
    position: relative;
    width: 1200px;
    height: 675px;
    overflow: hidden;
    background: var(--poster-red);
  }
  .poster-frame {
    position: absolute;
    left: 66px;
    top: 49px;
    width: 1058px;
    height: 570px;
    border: 7px solid var(--frame-grey);
    border-radius: 3px;
    box-sizing: border-box;
  }
  .quote {
    position: absolute;
    left: 0;
    top: 0;
    width: 1200px;
    margin: 0;
    color: var(--ink-white);
    font-family: "Josefin Sans", sans-serif;
    font-weight: 600;
    text-transform: uppercase;
    white-space: nowrap;
  }
  .quote-line {
    display: block;
    position: absolute;
    left: 0;
    width: 1200px;
    text-align: center;
    font-size: 88px;
    line-height: 1;
    letter-spacing: 0;
    transform: scaleX(0.6);
    transform-origin: 600px 50%;
  }
  .quote-line--first { top: 193px; }
  .quote-line--second { top: 315px; }
  .initial {
    font-size: 110px;
    line-height: 0;
  }
  .attribution {
    position: absolute;
    left: 0;
    top: 468px;
    width: 1200px;
    margin: 0;
    text-align: center;
    color: var(--ink-white);
    font-family: "Carlito", sans-serif;
    font-size: 54px;
    letter-spacing: 1px;
    line-height: 1;
    white-space: nowrap;
  }
</style>
</head>
<body>
  <main class="poster">
    <div class="poster-frame"></div>
    <blockquote class="quote">
      <span class="quote-line quote-line--first"><span class="initial">I</span>t’s hard to beat a person</span>
      <span class="quote-line quote-line--second">who never gives up.</span>
    </blockquote>
    <p class="attribution">Dale Mercer, Baseball Legend</p>
  </main>
</body>
</html>
```